Business Card for a mobile physiotherapy company

I need a layout for a business card for a mobile physiotherapy company.
Slogan is "Mobile Physiotherapy - Your Road To Recovery"
Phone number is 867-555-0142
Email VardenTherapy@postnest.ca (subject to change with website)
Website www.VardenTherapy.ca
My name and credentials: Luke Varden Luke Varden, BSc(kin), MPT, CAFCI, IMS
Information maybe included: Direct Billing, Services including Physiotherapy, IMS, acupuncture
Maybe include facebook and instagram logos
One side with the logo clean and sharp
Other side with details, try not to look too busy, keep everything concise

```html
<!DOCTYPE html>
<html lang="en">
<head>
<meta charset="utf-8">
<title>Varden Therapy – Business Card</title>
<link rel="stylesheet" href="https://fonts.googleapis.com/css2?family=Tinos:wght@400;700&family=Roboto:ital,wght@0,400;1,400&display=swap">
<style>
  :root {
    --navy: #2d4a72;
    --green: #0d5045;
    --ink: #4a4f57;
    --paper: #ffffff;
    --backdrop: #e8e5e0;
    --serif: "Tinos", "Times New Roman", serif;
    --sans: "Roboto", Arial, sans-serif;
  }
  * { box-sizing: border-box; margin: 0; padding: 0; }
  html, body { width: 1125px; height: 1200px; overflow: hidden; background: var(--backdrop); }
  .canvas { position: relative; width: 1125px; height: 1200px; }

  .card { position: absolute; left: 171px; width: 826px; height: 471px; box-shadow: 0 4px 10px rgba(0,0,0,.25); overflow: hidden; }
  .card--front { top: 106px; background: var(--paper); }
  .card--back { top: 640px; background: var(--navy); }

  /* front: details */
  .holder { position: absolute; left: 58px; top: 68px; font-family: var(--serif); }
  .holder__name { font-size: 31px; font-weight: 700; color: var(--navy); letter-spacing: .5px; line-height: 1; }
  .holder__credentials { font-size: 19px; color: var(--navy); margin-top: 4px; }
  .holder__billing { font-size: 21px; color: var(--green); margin-top: 3px; }

  .contacts { position: absolute; left: 58px; top: 336px; list-style: none; font-family: var(--serif); font-size: 19px; color: var(--ink); }
  .contacts li { display: flex; align-items: center; height: 27px; }
  .contacts svg { width: 17px; height: 17px; margin-right: 10px; fill: var(--navy); flex: none; }

  /* front: brand column */
  .brand-band { position: absolute; left: 520px; top: 0; width: 240px; height: 320px; background: var(--navy); }
  .social { position: absolute; top: 78px; left: 0; width: 100%; display: flex; justify-content: center; gap: 5px; }
  .social__dot { width: 37px; height: 37px; border-radius: 50%; background: var(--paper); }
  .brand-name { position: absolute; left: 520px; top: 350px; width: 240px; text-align: center; font-family: var(--serif); font-size: 27px; font-weight: 700; color: var(--green); line-height: 1; white-space: nowrap; }

  /* back */
  .back-name { position: absolute; top: 195px; left: 0; width: 100%; text-align: center; font-family: var(--serif); font-size: 64px; font-weight: 700; color: var(--paper); line-height: 1; }
  .tagline { position: absolute; top: 362px; left: 0; width: 100%; text-align: center; font-family: var(--sans); color: var(--paper); }
  .tagline__slogan { font-size: 20px; font-style: italic; }
  .tagline__services { font-size: 20px; margin-top: 6px; }
</style>
</head>
<body>
<main class="canvas">
  <section class="card card--front" aria-label="Card front">
    <div class="holder">
      <p class="holder__name">LUKE VARDEN</p>
      <p class="holder__credentials">BSc(kin), MPT, CAFCI, IMS</p>
      <p class="holder__billing">Direct Billing</p>
    </div>
    <ul class="contacts">
      <li><svg viewBox="0 0 24 24"><path d="M6.6 10.8a15.1 15.1 0 0 0 6.6 6.6l2.2-2.2a1 1 0 0 1 1-.25 11.4 11.4 0 0 0 3.6.57 1 1 0 0 1 1 1V20a1 1 0 0 1-1 1A17 17 0 0 1 3 4a1 1 0 0 1 1-1h3.5a1 1 0 0 1 1 1c0 1.25.2 2.45.57 3.57a1 1 0 0 1-.25 1z"/></svg>867-555-0142</li>
      <li><svg viewBox="0 0 24 24"><path d="M2 6v13h20V6l-10 7.5z M2.5 5h19L12 12z"/></svg>VardenTherapy@postnest.ca</li>
      <li><svg viewBox="0 0 24 24"><circle cx="12" cy="12" r="10"/><path d="M7 6c2 1 3 3 2 5s1 3 2 5M15 4c-1 2 0 4 2 4s3 2 3 4M14 20c0-2 1-3 3-3" stroke="#fff" stroke-width="1.6" fill="none"/></svg>www.VardenTherapy.ca</li>
    </ul>
    <div class="brand-band">
      <div class="social" aria-label="Social media">
        <span class="social__dot"></span>
        <span class="social__dot"></span>
      </div>
    </div>
    <p class="brand-name">Varden Therapy</p>
  </section>

  <section class="card card--back" aria-label="Card back">
    <p class="back-name">Varden Therapy</p>
    <div class="tagline">
      <p class="tagline__slogan">Mobile Physiotherapy - Your Road To Recovery</p>
      <p class="tagline__services">Physiotherapy • IMS • Acupuncture</p>
    </div>
  </section>
</main>
</body>
</html>
```